U.S. Popcorn company needs business cards

We are a popcorn company that manufactures popcorn and sells it to grocery stores worldwide. Our theme is "Americana" and our logo is U.S. route 66 which is the most famous highway in the U.S.

We would like the design to be simple and to use both sides. On the back side we would like to see just the logo and website. The front would be normal details

Target Market(s)

Wholesalers, grocers and distributors

Industry/Entity Type

Manufacture

Contact Information for Business Card

Business name: Prairie Lantern Popcorn
Phone: +1 555 308 4726
Email: Dale@prairielanternpopcorn.com
website: www.prairielanternpopcorn.com
Tag Line: "POPular for a reason"
Name: Dale Whitcombe
Title: Founder/President

Requirements
Must have
• Either this design should be fun or clean and simple. I will let you show me your thougths.
Nice to have
• Anything that ties in the real Hwy Route 66.
• Colors might need to be red, white and blue incorporated.
Should not have
• Not be too busy.

```html
<!DOCTYPE html>
<html lang="en">
<head>
<meta charset="utf-8">
<title>Prairie Lantern Popcorn – Business Card</title>
<link rel="stylesheet" href="https://fonts.googleapis.com/css2?family=Questrial&family=Mulish:wght@400;800&display=swap">
<style>
  :root {
    --page: #e4e2df;
    --navy: #1e3a78;
    --navy-deep: #17306a;
    --red: #d8231f;
    --paper: #eef0f2;
    --ink-light: #e8ecf4;
    --ink-soft: #cfd7e6;
  }
  * { box-sizing: border-box; margin: 0; padding: 0; }
  html, body {
    width: 1200px; height: 1010px; overflow: hidden;
    background: var(--page);
  }
  .card {
    position: absolute; left: 100px; top: 215px;
    width: 1000px; height: 580px;
    background: var(--paper);
    box-shadow: 0 10px 30px rgba(0,0,0,.18);
    overflow: hidden;
    font-family: "Questrial", "Mulish", sans-serif;
  }
  .card-shapes { position: absolute; inset: 0; width: 100%; height: 100%; }
  .holder-name {
    position: absolute; left: 44px; top: 80px;
    font-size: 41px; font-weight: 400; letter-spacing: .3px;
    color: var(--ink-light);
    font-family: "Mulish", sans-serif; font-weight: 800;
  }
  .holder-title {
    position: absolute; left: 44px; top: 134px;
    font-size: 23px; color: var(--ink-soft);
  }
  .contact-list {
    position: absolute; left: 44px; top: 362px;
    list-style: none;
  }
  .contact-list li {
    display: flex; align-items: center; gap: 18px;
    height: 34px;
    font-size: 24px; color: var(--ink-soft);
  }
  .contact-list svg { width: 24px; height: 20px; fill: var(--ink-soft); flex: none; }
  .tagline {
    position: absolute; left: 44px; top: 492px;
    font-size: 27px; color: #f4c9c4;
  }
  .tagline b { font-family: "Mulish", sans-serif; font-weight: 800; color: #fff; }
  .brand-name {
    position: absolute; left: 650px; top: 225px; width: 300px;
    text-align: center;
    font-family: "Questrial", sans-serif;
    font-size: 40px; line-height: 1.15;
    color: var(--navy);
  }
</style>
</head>
<body>
  <div class="card">
    <svg class="card-shapes" viewBox="0 0 1000 580" preserveAspectRatio="none" aria-hidden="true">
      <defs>
        <clipPath id="blue-area">
          <path d="M0 0 H622 C545 150 520 400 616 580 H0 Z"/>
        </clipPath>
        <linearGradient id="blue-fill" x1="0" y1="0" x2="1" y2="0">
          <stop offset="0" stop-color="#1c3672"/>
          <stop offset="1" stop-color="#254489"/>
        </linearGradient>
      </defs>
      <path d="M0 0 H622 C545 150 520 400 616 580 H0 Z" fill="url(#blue-fill)"/>
      <g clip-path="url(#blue-area)">
        <rect x="0" y="482" width="1000" height="62" fill="var(--red)"/>
        <rect x="0" y="544" width="1000" height="36" fill="var(--navy-deep)"/>
      </g>
      <path d="M676 0 H694 C600 120 570 330 612 510 C556 340 572 130 676 0 Z" fill="var(--red)"/>
    </svg>

    <div class="holder-name">Dale Whitcombe</div>
    <div class="holder-title">Founder/President</div>

    <ul class="contact-list">
      <li>
        <svg viewBox="0 0 24 20"><path d="M2 6c0-3 5-5 10-5s10 2 10 5v2h-5V5.5C15 4.8 13.5 4.5 12 4.5S9 4.8 7 5.5V8H2z"/><path d="M6 9h12l3 9H3z"/><circle cx="12" cy="13.5" r="2.6" fill="#254489"/></svg>
        <span>+1 555 308 4726</span>
      </li>
      <li>
        <svg viewBox="0 0 24 20"><path d="M1 3h22v14H1z"/><path d="M1 3l11 8 11-8" fill="none" stroke="#254489" stroke-width="1.8"/></svg>
        <span>Dale@prairielanternpopcorn.com</span>
      </li>
      <li>
        <svg viewBox="0 0 24 20"><circle cx="12" cy="10" r="9"/><path d="M3 10h18M12 1v18M12 1c-5 5-5 13 0 18M12 1c5 5 5 13 0 18" fill="none" stroke="#254489" stroke-width="1.4"/></svg>
        <span>prairielanternpopcorn.com</span>
      </li>
    </ul>

    <div class="tagline">"<b>POP</b>ular for a reason"</div>

    <div class="brand-name">Prairie Lantern Popcorn</div>
  </div>
</body>
</html>
```